Website - Loretta Dubrow

I need a website that has multiple pages and easy for me to update pictures, content and blogs as an ongoing basis’s.
It will have videos and needs to be compatible to view easily and aesthetically on mobile phones.
Please refer to this website for inspiration www.quinnafernsby.com

Coding

Coded - Design and coding required

Number of Pages Required

5+ page

Other font styles liked:
• Refer to website provided as inspiration

Requirements
Must have
• Please use stock images for now to do design, but I will be providing all imagery, videos and content

```html
<!DOCTYPE html>
<html lang="en">
<head>
<meta charset="utf-8">
<title>Loretta Dubrow</title>
<link rel="stylesheet" href="https://fonts.googleapis.com/css2?family=Quicksand:wght@400;500;600;700&family=Tinos&family=Josefin+Sans:wght@300;400&display=swap">
<style>
:root{
  --ink:#1e2126;
  --muted:#3b3f46;
  --blue:#3a9be8;
  --blue-deep:#1b7fe0;
  --blue-bright:#2fabf4;
  --sky:#dcebf8;
  --sky-soft:#e6f0f9;
  --band:#4a9ae2;
  --white:#ffffff;
  --night:#0d0c10;
  --line:#c9ccd1;
}
*{margin:0;padding:0;box-sizing:border-box}
html,body{width:1200px;height:3653px;overflow:hidden;background:var(--white)}
body{position:relative;font-family:'Quicksand',sans-serif;color:var(--ink)}
.abs{position:absolute}
.serif{font-family:'Tinos',serif;font-weight:400}
.logo{font-family:'Josefin Sans',sans-serif;font-weight:300;font-size:32px;letter-spacing:2px;color:var(--ink)}
.nav a{position:absolute;font-size:15px;font-weight:500;color:var(--ink);text-decoration:none}
.ring{position:absolute;border-radius:50%}
.photo{position:absolute}
.btn{position:absolute;display:flex;align-items:center;justify-content:center;border-radius:24px;
  background:linear-gradient(90deg,var(--blue-bright),var(--blue-deep));color:var(--white);
  font-size:13px;font-weight:700;letter-spacing:.5px;box-shadow:0 4px 10px rgba(27,127,224,.25)}
.hero-text .kicker{font-size:14px;letter-spacing:1.5px;font-weight:500}
.hero-text h1{font-size:31px;line-height:44px;margin-top:12px;letter-spacing:.5px}
.hero-text p{font-size:15px;line-height:23px;margin-top:12px;font-weight:500}
.section-title{font-size:35px;letter-spacing:1px}
.section-title span{color:var(--blue)}
.rule{position:absolute;height:3px;background:var(--blue)}
.about-copy{font-size:15.5px;line-height:25.7px;font-weight:500;letter-spacing:.2px}
.card h3{font-family:'Tinos',serif;font-weight:400;font-size:18.5px;line-height:30px;letter-spacing:.5px}
.card p{font-size:14.5px;line-height:23px;margin-top:6px;font-weight:500;color:var(--muted)}
.card .more{display:flex;align-items:center;gap:14px;margin-top:12px;color:var(--blue-deep);font-size:14px;font-weight:700;letter-spacing:.5px}
.grid-tile{position:absolute;width:221px;height:221px;border-radius:3px}
.signup h2{font-size:31px;line-height:44px;color:var(--white);letter-spacing:.5px}
.signup p{font-size:16px;color:var(--white);margin-top:10px;font-weight:500}
.field{position:absolute;background:var(--white);border-radius:22px;font-size:12px;letter-spacing:1px;color:var(--muted);display:flex;align-items:center;padding-left:24px;font-weight:500}
</style>
</head>
<body>

<!-- header -->
<header>
  <div class="abs logo" style="left:111px;top:22px">Loretta Dubrow</div>
  <nav class="nav">
    <a style="left:750px;top:28px">About</a>
    <a style="left:831px;top:28px">Blog</a>
    <a style="left:898px;top:28px">Stories</a>
    <a style="left:984px;top:28px">Contact</a>
  </nav>
  <div class="ring" style="left:1064px;top:26px;width:24px;height:24px;border:2.5px solid #d9457a" aria-label="Social"></div>
</header>

<!-- hero -->
<section class="hero">
  <div class="photo" role="img" aria-label="Faded portrait of Loretta on a lakeside jetty" style="left:0;top:75px;width:516px;height:579px;background:linear-gradient(160deg,#e9f1f9,#d7e6f4 55%,#e4edf6)"></div>
  <div class="abs" style="left:516px;top:75px;width:684px;height:579px;background:var(--sky);border-left:3px solid #9cc8ef;border-top:2px solid #9cc8ef;border-bottom:3px solid #9cc8ef"></div>
  <div class="photo" role="img" aria-label="Loretta in a pink dress on a wooden jetty by the water" style="left:533px;top:77px;width:539px;height:574px;background:linear-gradient(180deg,#b9c4cf 0%,#7f8c88 22%,#4e5658 45%,#6d675f 75%,#8a8580 100%)"></div>
  <div class="photo" role="img" aria-label="White jetty post" style="left:1072px;top:77px;width:128px;height:574px;background:linear-gradient(90deg,#c9cdd0,#eef0f1 40%,#d6d9dc)"></div>
  <div class="abs hero-text" style="left:111px;top:250px;width:380px">
    <div class="kicker">LORETTA DUBROW</div>
    <h1 class="serif">MISS COASTAL STARS NATIONAL FINALIST 2021</h1>
    <p>Omnis iste natus error sit voluptatem accusantium doloremque</p>
  </div>
</section>

<!-- about -->
<section class="about">
  <div class="photo" role="img" aria-label="Portrait of Loretta smiling in a white top" style="left:34px;top:730px;width:407px;height:510px;background:linear-gradient(135deg,#e8e6e3,#cdbfb2 45%,#9a7760 70%,#ece9e6)"></div>
  <div class="abs" style="left:384px;top:980px;width:223px;height:280px;background:var(--white)"></div>
  <div class="photo" role="img" aria-label="Loretta wearing a crown and sash with flowers" style="left:390px;top:986px;width:217px;height:274px;background:linear-gradient(180deg,#e7e1e6,#d8c4c8 40%,#2e7a66 75%,#2a5e52)"></div>
  <h2 class="abs section-title serif" style="left:658px;top:830px">ABOUT <span>ME</span></h2>
  <div class="rule" style="left:658px;top:881px;width:73px"></div>
  <p class="abs about-copy" style="left:658px;top:903px;width:430px">Perspiciatis unde omnis iste natus error sit volup tatem accusantium doloremque laudantium totam rem aperiam, eaque ipsa quae ab illo inventore veritatis et quasi architecto beatae vitae dicta sunt explicabo. Nemo enim ipsam voluptatem quia voluptas sit&nbsp; numquam eius modi tempora incidunt ut labore et dolore magnam aliquam</p>
  <div class="btn" style="left:658px;top:1105px;width:162px;height:43px">LEARN MORE</div>
</section>

<!-- video -->
<section class="video">
  <div class="photo" role="img" aria-label="Video still of Loretta in a sparkling dress on a dark starry stage" style="left:0;top:1346px;width:1200px;height:387px;background:radial-gradient(ellipse 220px 260px at 600px 190px,#5a4a4c,#241d22 60%,var(--night) 100%)"></div>
  <svg class="abs" style="left:543px;top:1482px" width="114" height="114" viewBox="0 0 114 114" aria-label="Play video">
    <circle cx="57" cy="57" r="54" fill="none" stroke="#fff" stroke-width="2.5"/>
    <path d="M48 41 L73 57 L48 73 Z" fill="#fff"/>
  </svg>
</section>

<!-- blog -->
<section class="blog">
  <div class="abs" style="left:0;top:1733px;width:1200px;height:763px;background:var(--sky)"></div>
  <h2 class="abs section-title serif" style="left:0;top:1810px;width:1200px;text-align:center">LATEST <span>BLOG</span></h2>
  <div class="rule" style="left:563px;top:1861px;width:74px"></div>

  <article class="abs card" style="left:111px;top:1888px;width:307px">
    <div role="img" aria-label="Loretta smiling in a white t-shirt by a window" style="height:274px;border-radius:3px;background:linear-gradient(135deg,#e6e8e9,#b7a596 50%,#f0efee)"></div>
    <h3 style="margin-top:22px">PERSPICIATIS UNDE OMNIS ISTE NATUS ERROR</h3>
    <p>Omnis iste natus error sit voluptatem accusantium doloremque</p>
    <div class="more">Read More <svg width="64" height="12" viewBox="0 0 64 12"><path d="M0 6H62M55 1L62 6L55 11" fill="none" stroke="currentColor" stroke-width="2"/></svg></div>
  </article>
  <article class="abs card" style="left:445px;top:1888px;width:308px">
    <div role="img" aria-label="Black and white photo of Loretta in boots" style="height:274px;border-radius:3px;background:linear-gradient(135deg,#d8d8d8,#7c7c7c 50%,#e6e6e6)"></div>
    <h3 style="margin-top:22px">PERSPICIATIS UNDE OMNIS ISTE NATUS ERROR</h3>
    <p>Omnis iste natus error sit voluptatem accusantium doloremque</p>
    <div class="more">Read More <svg width="64" height="12" viewBox="0 0 64 12"><path d="M0 6H62M55 1L62 6L55 11" fill="none" stroke="currentColor" stroke-width="2"/></svg></div>
  </article>
  <article class="abs card" style="left:779px;top:1888px;width:307px">
    <div role="img" aria-label="Loretta standing on rocks in a city park" style="height:274px;border-radius:3px;background:linear-gradient(180deg,#9aa3ad,#6e6f6b 45%,#8a8580)"></div>
    <h3 style="margin-top:22px">PERSPICIATIS UNDE OMNIS ISTE NATUS ERROR</h3>
    <p>Omnis iste natus error sit voluptatem accusantium doloremque</p>
    <div class="more">Read More <svg width="64" height="12" viewBox="0 0 64 12"><path d="M0 6H62M55 1L62 6L55 11" fill="none" stroke="currentColor" stroke-width="2"/></svg></div>
  </article>

  <div class="btn" style="left:518px;top:2367px;width:163px;height:42px">VIEW MORE</div>
</section>

<!-- feed -->
<section class="feed">
  <div class="grid-tile" role="img" aria-label="Grey tote bag" style="left:111px;top:2588px;background:linear-gradient(135deg,#ebe7e2,#a8a29b 55%,#ddd6cd)"></div>
  <div class="grid-tile" role="img" aria-label="Close-up portrait of Loretta" style="left:362px;top:2588px;background:linear-gradient(135deg,#7b5a45,#c79d80 50%,#8c6a55)"></div>
  <div class="grid-tile" role="img" aria-label="Loretta sitting on a kitchen bench" style="left:613px;top:2588px;background:linear-gradient(135deg,#ecebea,#b5bccb 55%,#e8e6e3)"></div>
  <div class="grid-tile" role="img" aria-label="Loretta in a ruffled skirt beside a pink stand" style="left:864px;top:2588px;background:linear-gradient(135deg,#e4e2df,#caa9b1 55%,#e7d6d9)"></div>
  <div class="grid-tile" role="img" aria-label="Loretta taking a mirror photo" style="left:111px;top:2841px;background:linear-gradient(135deg,#d2c6bb,#6f5242 55%,#d9d3cd)"></div>
  <div class="grid-tile" role="img" aria-label="Loretta holding a drink" style="left:362px;top:2841px;background:linear-gradient(135deg,#a9cfe0,#c69a82 55%,#9ac4d8)"></div>
  <div class="grid-tile" role="img" aria-label="Loretta in a floral top, darkened on hover" style="left:613px;top:2841px;background:linear-gradient(135deg,#5a5353,#3f3a3b 60%,#4d4647)"></div>
  <div class="ring" style="left:708px;top:2936px;width:30px;height:30px;border:2.5px solid #fff"></div>
  <div class="grid-tile" role="img" aria-label="Loretta in a blue jumper outdoors" style="left:864px;top:2841px;background:linear-gradient(135deg,#c8cfc0,#8a6a58 45%,#b9c6e4)"></div>
  <div class="btn" style="left:518px;top:3099px;width:163px;height:42px">VIEW MORE</div>
</section>

<!-- signup -->
<section class="signup">
  <div class="abs" style="left:0;top:3230px;width:1200px;height:251px;background:var(--band)"></div>
  <div class="abs" style="left:111px;top:3294px;width:560px">
    <h2 class="serif">SIGN UP WITH YOUR EMAIL ADDRESS TO RECEIVE NEWS AND UPDATES.</h2>
    <p>Perspiciatis unde omnis iste natus error sit</p>
  </div>
  <div class="field" style="left:679px;top:3299px;width:409px;height:42px">ENTER MAIL</div>
  <div class="field" style="left:679px;top:3370px;width:162px;height:42px;padding:0;justify-content:center;color:var(--blue-deep);font-weight:700;font-size:13px">SIGN UP</div>
</section>

<!-- footer -->
<footer>
  <div class="abs logo" style="left:111px;top:3520px">Loretta Dubrow</div>
  <nav class="nav">
    <a style="left:505px;top:3527px">About</a>
    <a style="left:597px;top:3527px">Blog</a>
    <a style="left:677px;top:3527px">Stories</a>
    <a style="left:776px;top:3527px">Contact</a>
  </nav>
  <div class="ring" style="left:1008px;top:3510px;width:54px;height:54px;border:1.5px solid var(--blue)"></div>
  <div class="ring" style="left:1026px;top:3528px;width:18px;height:18px;border:2px solid var(--blue)"></div>
  <div class="abs" style="left:111px;top:3590px;width:977px;height:1px;background:var(--line)"></div>
  <div class="abs" style="left:0;top:3609px;width:1200px;text-align:center;font-size:14px;font-weight:500">Copyright © 2021 - All rights reserved</div>
  <svg class="abs" style="left:1131px;top:3578px" width="18" height="26" viewBox="0 0 18 26" aria-label="Back to top"><path d="M9 25V2M2 9L9 2L16 9" fill="none" stroke="var(--blue-deep)" stroke-width="2"/></svg>
</footer>

</body>
</html>
```